Before the kettle boils, pocast with content in its majority of technology

Page dedicated to a pocast with content in its majority of technology. The page also contains the chapters of the podcast (pluggin vocalink) will also contain news. Preferably Worpress. There is already a very basic page with a simple theme, the logo and little more, I would like something more professional. Www.lamparadebolsillo.com The logo does not want to change.

Target Market(s)

Anyone

Colors

Designer to choose colors to be used in the design.

Requirements
Must have
• You can put the vocalink pluggin with the podcast chapters

```html
<!DOCTYPE html>
<html lang="es">
<head>
<meta charset="utf-8">
<title>Before the kettle boils — Podcast de tecnología</title>
<link rel="stylesheet" href="https://fonts.googleapis.com/css2?family=Oswald:wght@400;500&family=Open+Sans:wght@400;600&display=swap">
<style>
:root{
  --ink:#222222;
  --header:#232323;
  --footer:#2b2b2b;
  --orange:#f07b13;
  --text:#333333;
  --muted:#8a8a8a;
  --panel:#f4f4f4;
  --line:#e2e2e2;
  --wave:#cfcfcf;
  --share:#9aa3ad;
  --white:#ffffff;
}
*{box-sizing:border-box;margin:0;padding:0}
html,body{width:1200px;height:2862px;overflow:hidden;background:var(--white)}
body{font-family:"Open Sans",Arial,sans-serif;color:var(--text);position:relative}

/* header */
.site-header{position:absolute;left:0;top:0;width:1200px;height:191px;background:var(--header)}
.brand{position:absolute;left:130px;top:40px;width:260px}
.brand-dot{width:60px;height:60px;border-radius:50%;background:var(--orange);margin-left:90px}
.brand-name{font-family:"Oswald",Arial,sans-serif;font-weight:500;color:var(--orange);font-size:25px;text-transform:uppercase;line-height:1;margin-top:26px;white-space:nowrap}
.brand-tag{font-family:"Oswald",Arial,sans-serif;color:var(--white);font-size:20px;text-transform:uppercase;line-height:1.1;letter-spacing:.5px}
.search{position:absolute;left:843px;top:53px;width:223px;height:40px;border:1px solid #666;display:flex;align-items:center;justify-content:space-between;padding:0 14px;font-family:"Oswald",Arial,sans-serif;color:#aaa;font-size:15px}
.main-nav{position:absolute;top:141px;left:784px;font-family:"Oswald",Arial,sans-serif;font-size:16px;text-transform:uppercase}
.main-nav a{color:#b5b5b5;text-decoration:none;position:absolute;white-space:nowrap}
.main-nav a.current{color:var(--white)}

/* hero */
.hero{position:absolute;left:0;top:191px;width:1200px;height:423px;background:linear-gradient(100deg,#4d3f32 0%,#8a7b68 30%,#c9b48f 55%,#e8d2a4 75%,#a59073 100%)}
.hero-arrow{position:absolute;top:195px;width:30px;height:30px;border-radius:50%;background:rgba(0,0,0,.35)}
.hero-card{position:absolute;left:788px;top:63px;width:278px;height:295px;background:rgba(255,255,255,.92);padding:22px 24px}
.meta{font-family:"Oswald",Arial,sans-serif;font-size:14px;color:#777;text-transform:uppercase}
.hero-card h2{font-family:"Oswald",Arial,sans-serif;font-weight:400;color:var(--orange);font-size:23px;margin:4px 0 12px}
.hero-card p{font-size:11px;line-height:19px;color:#888}
.btn-ghost{display:inline-block;margin-top:20px;border:1px solid #ccc;padding:9px 16px;font-size:11px;color:#555}

/* posts */
.post{position:absolute;left:130px;width:635px;height:452px}
.post-top{display:flex;height:242px;background:var(--panel)}
.post-photo{width:242px;height:242px;flex:none}
.post-body{padding:22px 16px 22px 22px;min-width:0}
.post-body h3{font-family:"Oswald",Arial,sans-serif;font-weight:400;color:var(--orange);font-size:20px;line-height:28px;margin:3px 0 14px;white-space:nowrap;letter-spacing:-.2px}
.post-body p{font-size:11px;line-height:20px;color:#777}
.player{display:flex;height:166px;background:#ececec;margin-top:10px;padding:0 0 0 10px;align-items:center}
.player-art{width:232px;height:152px;flex:none}
.player-main{flex:1;padding:10px 28px 10px 22px;height:166px}
.player-head{display:flex;align-items:center;height:48px}
.play{width:38px;height:38px;border-radius:50%;background:var(--orange);flex:none;display:flex;align-items:center;justify-content:center}
.episode{margin-left:12px;flex:1}
.episode strong{font-family:"Oswald",Arial,sans-serif;font-weight:400;font-size:16px;color:var(--ink);display:block}
.host-name{font-family:"Oswald",Arial,sans-serif;font-size:18px;color:#444}
.wave-box{margin-top:12px;background:var(--white);height:92px;position:relative;padding:4px 8px}
.wave-box .times{display:flex;justify-content:space-between;font-size:11px;color:#888}
.wave-box svg{position:absolute;left:8px;bottom:4px}
.share-row{display:flex;align-items:center;margin-top:23px;height:30px}
.share-dot{width:28px;height:28px;border-radius:50%;background:var(--share);margin-right:7px;flex:none;display:flex;align-items:center;justify-content:center}
.share-dot.util{background:#d6d6d6}
.filed{margin-left:auto;font-size:11px;color:#999}
.filed b{font-weight:400;color:var(--ink)}

/* sidebar */
.widget{position:absolute;left:788px;width:278px;background:var(--panel)}
.widget-head{display:flex;justify-content:space-between;align-items:baseline;padding:18px 22px 12px;border-bottom:1px solid var(--line)}
.widget-head h4{font-family:"Oswald",Arial,sans-serif;font-weight:400;color:var(--orange);font-size:22px}
.widget-head span{font-family:"Oswald",Arial,sans-serif;font-size:11px;color:#777;text-decoration:underline}
.widget ul{margin:0;padding:0}
.widget li{list-style:none;padding:12px 22px 10px;border-bottom:1px solid var(--line)}
.widget li:last-child{border-bottom:0}
.widget li strong{font-family:"Oswald",Arial,sans-serif;font-weight:400;font-size:14px;color:var(--ink);display:block;margin-bottom:4px;white-space:nowrap}
.widget li span{font-size:10.5px;line-height:17px;color:#888;display:block}
.promo{position:absolute;left:788px;top:1541px;width:278px;height:199px;background:linear-gradient(180deg,#d9eefb 0%,#3aa3dc 55%,#1783c4 100%);text-align:center;padding-top:24px}
.promo .close{position:absolute;right:8px;top:4px;font-size:10px;color:#fff}
.promo h5{font-family:"Open Sans",Arial,sans-serif;font-weight:600;font-size:21px;line-height:26px;color:#1d1d1d}
.promo p{font-size:13px;line-height:17px;color:#fff;margin-top:8px}
.promo .cta{display:inline-block;margin-top:12px;background:var(--orange);color:#1d1d1d;font-weight:600;font-size:16px;padding:7px 22px;border-radius:3px}
.newsletter{position:absolute;left:788px;top:1770px;width:278px}
.newsletter h4{font-family:"Oswald",Arial,sans-serif;font-weight:400;color:var(--orange);font-size:22px}
.newsletter form{display:flex;margin-top:6px;height:40px}
.newsletter .field{flex:1;border:1px solid #ddd;font-size:11px;color:#aaa;padding:12px 10px}
.newsletter .go{width:80px;background:#c8c8c8;font-family:"Oswald",Arial,sans-serif;font-size:15px;color:#222;display:flex;align-items:center;justify-content:center}

/* pagination */
.pager{position:absolute;left:130px;top:2654px;display:flex;gap:4px}
.pager span{width:30px;height:30px;background:#e8e8e8;font-size:12px;color:#666;display:flex;align-items:center;justify-content:center}
.pager span.on{background:#444;color:#fff}
.pager span.gap{margin-left:10px}

/* footer */
.site-footer{position:absolute;left:0;top:2764px;width:1200px;height:98px;background:var(--footer)}
.foot-links{position:absolute;left:130px;top:28px;font-size:11px;color:#ccc}
.foot-copy{position:absolute;left:130px;top:56px;font-size:11px;color:#999}
.foot-share{position:absolute;left:740px;top:33px;display:flex}
.foot-share .share-dot{background:#6d7782}
</style>
</head>
<body>

<header class="site-header">
  <div class="brand">
    <div class="brand-dot"></div>
    <div class="brand-name">Before the kettle boils</div>
    <div class="brand-tag">Podcast de tecnología</div>
  </div>
  <div class="search"><span>Search</span>
    <svg width="13" height="13" viewBox="0 0 13 13"><circle cx="5.5" cy="5.5" r="4" fill="none" stroke="#aaa" stroke-width="1.6"/><line x1="8.5" y1="8.5" x2="12" y2="12" stroke="#aaa" stroke-width="1.8"/></svg>
  </div>
  <nav class="main-nav">
    <a class="current" style="left:0">Home</a>
    <a style="left:63px">About</a>
    <a style="left:132px">Categories</a>
    <a style="left:229px">Contact</a>
  </nav>
</header>

<section class="hero" role="img" aria-label="Foto: hombre con auriculares escuchando música en la calle al atardecer">
  <div class="hero-arrow" style="left:20px"><svg width="30" height="30"><path d="M17 9 L11 15 L17 21" fill="none" stroke="#fff" stroke-width="2.5"/></svg></div>
  <div class="hero-arrow" style="left:1148px"><svg width="30" height="30"><path d="M13 9 L19 15 L13 21" fill="none" stroke="#fff" stroke-width="2.5"/></svg></div>
  <article class="hero-card">
    <div class="meta">17 May, 2017 de Marlow</div>
    <h2>Phasellus egestas sem eget</h2>
    <p>Proin massa magna, suscipit semper pharetra sed, dignissim et eros. Vivamus eget dolor molestie mi venenatis accumsan nec vitae magna. Vivamus congue sollicitudin vestibulum. Etiam mi ipsum, ultrices nec luctus sit amet, posuere in sem. Ut sed porta orci, sit amet venenatis est.</p>
    <span class="btn-ghost">Read more</span>
  </article>
</section>

<article class="post" style="top:679px">
  <div class="post-top">
    <div class="post-photo" role="img" aria-label="Foto: auriculares blancos sobre fondo verde" style="background:linear-gradient(135deg,#cfd6d2,#7f938a 60%,#2f5a46)"></div>
    <div class="post-body">
      <div class="meta">17 May, 2017 de Marlow</div>
      <h3>¿Te gustan las series?¿Conoces serialo.tv?</h3>
      <p>Hola a tod@s! Hoy capítulo dedicado a los amantes de las series y las películas. Se trata del servicio de vídeo en streaming de la web serialo.tv portal dedicado al aprendizaje de inglés mediante el método de ver películas y series en inglés con subtítulos.</p>
    </div>
  </div>
  <div class="player">
    <div class="player-art" role="img" aria-label="Portada del episodio" style="background:#111"></div>
    <div class="player-main">
      <div class="player-head">
        <div class="play"><svg width="14" height="16"><path d="M2 1 L13 8 L2 15Z" fill="#fff"/></svg></div>
        <div class="episode"><strong>Un anuncio y una prueba</strong>
          <svg width="80" height="14" viewBox="0 0 80 14"><path d="M6 12 L1 6 A3 3 0 0 1 6 3 A3 3 0 0 1 11 6Z" fill="#555"/><rect x="30" y="3" width="11" height="7" rx="3" fill="#555"/><circle cx="60" cy="7" r="2" fill="#555"/><circle cx="66" cy="3" r="2" fill="#555"/><circle cx="66" cy="11" r="2" fill="#555"/></svg></div>
        <span class="host-name">Podvela</span>
      </div>
      <div class="wave-box"><div class="times"><span>00:00</span><span>05:28</span></div>
        <svg width="330" height="60" viewBox="0 0 330 60"><path d="M0 60 V40 L10 30 L20 38 L30 28 L40 35 L50 22 L60 34 L70 30 L80 38 L90 26 L100 33 L110 36 L120 24 L130 32 L140 30 L150 38 L160 27 L170 35 L180 31 L190 36 L200 25 L210 33 L220 28 L230 37 L240 30 L250 22 L260 30 L270 14 L280 26 L290 18 L300 30 L310 10 L320 22 L330 28 V60Z" fill="#cfcfcf"/></svg></div>
    </div>
  </div>
  <div class="share-row">
    <span class="share-dot"></span><span class="share-dot"></span><span class="share-dot"></span><span class="share-dot"></span><span class="share-dot"></span><span class="share-dot"></span><span class="share-dot"></span>
    <span class="share-dot util"><svg width="14" height="10"><rect x=".5" y=".5" width="13" height="9" fill="none" stroke="#555"/><path d="M1 1 L7 6 L13 1" fill="none" stroke="#555"/></svg></span>
    <span class="share-dot util"><svg width="14" height="12"><rect x="3" y="0" width="8" height="4" fill="#555"/><rect x="0" y="4" width="14" height="5" fill="#555"/><rect x="3" y="8" width="8" height="4" fill="#fff" stroke="#555"/></svg></span>
    <span class="filed">Publicado en <b>Podcast</b> &nbsp;|&nbsp; <b>Deja un comentario</b></span>
  </div>
</article>

<article class="post" style="top:1173px">
  <div class="post-top">
    <div class="post-photo" role="img" aria-label="Foto: micrófono de estudio antiguo" style="background:linear-gradient(160deg,#c9d9d2,#6fa99a 55%,#2f6a62)"></div>
    <div class="post-body">
      <div class="meta">17 May, 2017 de Marlow</div>
      <h3>¿Te gustan las series?¿Conoces serialo.tv?</h3>
      <p>Hola a tod@s! Hoy capítulo dedicado a los amantes de las series y las películas. Se trata del servicio de vídeo en streaming de la web serialo.tv portal dedicado al aprendizaje de inglés mediante el método de ver películas y series en inglés con subtítulos.</p>
    </div>
  </div>
  <div class="player">
    <div class="player-art" role="img" aria-label="Portada del episodio" style="background:#3b3f78"></div>
    <div class="player-main">
      <div class="player-head">
        <div class="play"><svg width="14" height="16"><path d="M2 1 L13 8 L2 15Z" fill="#fff"/></svg></div>
        <div class="episode"><strong>Un anuncio y una prueba</strong>
          <svg width="80" height="14" viewBox="0 0 80 14"><path d="M6 12 L1 6 A3 3 0 0 1 6 3 A3 3 0 0 1 11 6Z" fill="#555"/><rect x="30" y="3" width="11" height="7" rx="3" fill="#555"/><circle cx="60" cy="7" r="2" fill="#555"/><circle cx="66" cy="3" r="2" fill="#555"/><circle cx="66" cy="11" r="2" fill="#555"/></svg></div>
        <span class="host-name">Podvela</span>
      </div>
      <div class="wave-box"><div class="times"><span>00:00</span><span>05:28</span></div>
        <svg width="330" height="60" viewBox="0 0 330 60"><path d="M0 60 V40 L10 30 L20 38 L30 28 L40 35 L50 22 L60 34 L70 30 L80 38 L90 26 L100 33 L110 36 L120 24 L130 32 L140 30 L150 38 L160 27 L170 35 L180 31 L190 36 L200 25 L210 33 L220 28 L230 37 L240 30 L250 22 L260 30 L270 14 L280 26 L290 18 L300 30 L310 10 L320 22 L330 28 V60Z" fill="#cfcfcf"/></svg></div>
    </div>
  </div>
  <div class="share-row">
    <span class="share-dot"></span><span class="share-dot"></span><span class="share-dot"></span><span class="share-dot"></span><span class="share-dot"></span><span class="share-dot"></span><span class="share-dot"></span>
    <span class="share-dot util"><svg width="14" height="10"><rect x=".5" y=".5" width="13" height="9" fill="none" stroke="#555"/><path d="M1 1 L7 6 L13 1" fill="none" stroke="#555"/></svg></span>
    <span class="share-dot util"><svg width="14" height="12"><rect x="3" y="0" width="8" height="4" fill="#555"/><rect x="0" y="4" width="14" height="5" fill="#555"/><rect x="3" y="8" width="8" height="4" fill="#fff" stroke="#555"/></svg></span>
    <span class="filed">Publicado en <b>Podcast</b> &nbsp;|&nbsp; <b>Deja un comentario</b></span>
  </div>
</article>

<article class="post" style="top:1667px">
  <div class="post-top">
    <div class="post-photo" role="img" aria-label="Foto: mujer con auriculares en exterior" style="background:linear-gradient(150deg,#e3e7ea,#9aa3a8 50%,#2b2f33)"></div>
    <div class="post-body">
      <div class="meta">17 May, 2017 de Marlow</div>
      <h3>¿Te gustan las series?¿Conoces serialo.tv?</h3>
      <p>Hola a tod@s! Hoy capítulo dedicado a los amantes de las series y las películas. Se trata del servicio de vídeo en streaming de la web serialo.tv portal dedicado al aprendizaje de inglés mediante el método de ver películas y series en inglés con subtítulos.</p>
    </div>
  </div>
  <div class="player">
    <div class="player-art" role="img" aria-label="Portada del episodio" style="background:#f47b20"></div>
    <div class="player-main">
      <div class="player-head">
        <div class="play"><svg width="14" height="16"><path d="M2 1 L13 8 L2 15Z" fill="#fff"/></svg></div>
        <div class="episode"><strong>Un anuncio y una prueba</strong>
          <svg width="80" height="14" viewBox="0 0 80 14"><path d="M6 12 L1 6 A3 3 0 0 1 6 3 A3 3 0 0 1 11 6Z" fill="#555"/><rect x="30" y="3" width="11" height="7" rx="3" fill="#555"/><circle cx="60" cy="7" r="2" fill="#555"/><circle cx="66" cy="3" r="2" fill="#555"/><circle cx="66" cy="11" r="2" fill="#555"/></svg></div>
        <span class="host-name">Podvela</span>
      </div>
      <div class="wave-box"><div class="times"><span>00:00</span><span>05:28</span></div>
        <svg width="330" height="60" viewBox="0 0 330 60"><path d="M0 60 V40 L10 30 L20 38 L30 28 L40 35 L50 22 L60 34 L70 30 L80 38 L90 26 L100 33 L110 36 L120 24 L130 32 L140 30 L150 38 L160 27 L170 35 L180 31 L190 36 L200 25 L210 33 L220 28 L230 37 L240 30 L250 22 L260 30 L270 14 L280 26 L290 18 L300 30 L310 10 L320 22 L330 28 V60Z" fill="#cfcfcf"/></svg></div>
    </div>
  </div>
  <div class="share-row">
    <span class="share-dot"></span><span class="share-dot"></span><span class="share-dot"></span><span class="share-dot"></span><span class="share-dot"></span><span class="share-dot"></span><span class="share-dot"></span>
    <span class="share-dot util"><svg width="14" height="10"><rect x=".5" y=".5" width="13" height="9" fill="none" stroke="#555"/><path d="M1 1 L7 6 L13 1" fill="none" stroke="#555"/></svg></span>
    <span class="share-dot util"><svg width="14" height="12"><rect x="3" y="0" width="8" height="4" fill="#555"/><rect x="0" y="4" width="14" height="5" fill="#555"/><rect x="3" y="8" width="8" height="4" fill="#fff" stroke="#555"/></svg></span>
    <span class="filed">Publicado en <b>Podcast</b> &nbsp;|&nbsp; <b>Deja un comentario</b></span>
  </div>
</article>

<article class="post" style="top:2161px">
  <div class="post-top">
    <div class="post-photo" role="img" aria-label="Foto: locutor con micrófono en estudio con estanterías" style="background:linear-gradient(140deg,#e9dcc0,#b59a72 50%,#5b4a38)"></div>
    <div class="post-body">
      <div class="meta">17 May, 2017 de Marlow</div>
      <h3>¿Te gustan las series?¿Conoces serialo.tv?</h3>
      <p>Hola a tod@s! Hoy capítulo dedicado a los amantes de las series y las películas. Se trata del servicio de vídeo en streaming de la web serialo.tv portal dedicado al aprendizaje de inglés mediante el método de ver películas y series en inglés con subtítulos.</p>
    </div>
  </div>
  <div class="player">
    <div class="player-art" role="img" aria-label="Portada del episodio" style="background:#6dbb45"></div>
    <div class="player-main">
      <div class="player-head">
        <div class="play"><svg width="14" height="16"><path d="M2 1 L13 8 L2 15Z" fill="#fff"/></svg></div>
        <div class="episode"><strong>Un anuncio y una prueba</strong>
          <svg width="80" height="14" viewBox="0 0 80 14"><path d="M6 12 L1 6 A3 3 0 0 1 6 3 A3 3 0 0 1 11 6Z" fill="#555"/><rect x="30" y="3" width="11" height="7" rx="3" fill="#555"/><circle cx="60" cy="7" r="2" fill="#555"/><circle cx="66" cy="3" r="2" fill="#555"/><circle cx="66" cy="11" r="2" fill="#555"/></svg></div>
        <span class="host-name">Podvela</span>
      </div>
      <div class="wave-box"><div class="times"><span>00:00</span><span>05:28</span></div>
        <svg width="330" height="60" viewBox="0 0 330 60"><path d="M0 60 V40 L10 30 L20 38 L30 28 L40 35 L50 22 L60 34 L70 30 L80 38 L90 26 L100 33 L110 36 L120 24 L130 32 L140 30 L150 38 L160 27 L170 35 L180 31 L190 36 L200 25 L210 33 L220 28 L230 37 L240 30 L250 22 L260 30 L270 14 L280 26 L290 18 L300 30 L310 10 L320 22 L330 28 V60Z" fill="#cfcfcf"/></svg></div>
    </div>
  </div>
  <div class="share-row">
    <span class="share-dot"></span><span class="share-dot"></span><span class="share-dot"></span><span class="share-dot"></span><span class="share-dot"></span><span class="share-dot"></span><span class="share-dot"></span>
    <span class="share-dot util"><svg width="14" height="10"><rect x=".5" y=".5" width="13" height="9" fill="none" stroke="#555"/><path d="M1 1 L7 6 L13 1" fill="none" stroke="#555"/></svg></span>
    <span class="share-dot util"><svg width="14" height="12"><rect x="3" y="0" width="8" height="4" fill="#555"/><rect x="0" y="4" width="14" height="5" fill="#555"/><rect x="3" y="8" width="8" height="4" fill="#fff" stroke="#555"/></svg></span>
    <span class="filed">Publicado en <b>Podcast</b> &nbsp;|&nbsp; <b>Deja un comentario</b></span>
  </div>
</article>

<aside class="widget" style="top:679px">
  <div class="widget-head"><h4>Recent Post</h4><span>VIEW ALL</span></div>
  <ul>
    <li><strong>Cambio delogo</strong><span>¿Salta a la vista no?, pues sí, renovamos diseño del logo y algo en la web.</span></li>
    <li><strong>¿Te gustan las series?¿Conoces serialo.tv?</strong><span>¿Salta a la vista no?, pues sí, renovamos diseño del logo y algo en la web.</span></li>
    <li><strong>Un anuncio y una prueba</strong><span>¿Salta a la vista no?, pues sí, renovamos diseño del logo y algo en la web.</span></li>
    <li><strong>Seguridad en tu Mail</strong><span>¿Salta a la vista no?, pues sí, renovamos diseño del logo y algo en la web.</span></li>
  </ul>
</aside>

<aside class="widget" style="top:1110px">
  <div class="widget-head"><h4>Popular Post</h4><span>VIEW ALL</span></div>
  <ul>
    <li><strong>Cambio delogo</strong><span>¿Salta a la vista no?, pues sí, renovamos diseño del logo y algo en la web.</span></li>
    <li><strong>¿Te gustan las series?¿Conoces serialo.tv?</strong><span>¿Salta a la vista no?, pues sí, renovamos diseño del logo y algo en la web.</span></li>
    <li><strong>Un anuncio y una prueba</strong><span>¿Salta a la vista no?, pues sí, renovamos diseño del logo y algo en la web.</span></li>
    <li><strong>Seguridad en tu Mail</strong><span>¿Salta a la vista no?, pues sí, renovamos diseño del logo y algo en la web.</span></li>
  </ul>
</aside>

<aside class="promo">
  <span class="close">Close X</span>
  <h5>Get 10% off<br>your first order!</h5>
  <p>Sign up for our FREE newsletter to<br>get exclusive offers and coupons.</p>
  <span class="cta">Sign Up Now</span>
</aside>

<aside class="newsletter">
  <h4>Newsletter Subscribe</h4>
  <form><span class="field">Email Address</span><span class="go">Subscribe</span></form>
</aside>

<nav class="pager">
  <span class="on">1</span><span>2</span><span>3</span><span>4</span><span>5</span>
  <span class="gap">&lsaquo;</span><span>&rsaquo;</span>
</nav>

<footer class="site-footer">
  <div class="foot-links">Home &nbsp;|&nbsp; About &nbsp;|&nbsp; Categories &nbsp;|&nbsp; Contact</div>
  <div class="foot-copy">Copyright © 2017 Before the kettle boils. All rights reserved.</div>
  <div class="foot-share">
    <span class="share-dot"></span><span class="share-dot"></span><span class="share-dot"></span><span class="share-dot"></span><span class="share-dot"></span><span class="share-dot"></span><span class="share-dot"></span>
    <span class="share-dot util"><svg width="14" height="10"><rect x=".5" y=".5" width="13" height="9" fill="none" stroke="#555"/><path d="M1 1 L7 6 L13 1" fill="none" stroke="#555"/></svg></span>
    <span class="share-dot util"><svg width="14" height="12"><rect x="3" y="0" width="8" height="4" fill="#555"/><rect x="0" y="4" width="14" height="5" fill="#555"/><rect x="3" y="8" width="8" height="4" fill="#fff" stroke="#555"/></svg></span>
  </div>
</footer>

</body>
</html>
```